Commercial Auto Insurance Application and Commercial Property Insurance Application

Hi I need a fillable application for my business to send to potential clients for Commercial Auto Insurance and Commercial Property Insurance. I have attached an example application I currently use for another line of insurance.
Commercial Auto Insurance Application
On the first page I would need the following:
- Business Name: (fill in area for text)
- Effective Date: (fill in area for text)
- How do you structure your business? (Check box for “Sole Proprietor”, “Partnership”, “Corporation”, “LLC”)
- Contact Name: (fill in area for text) / Phone Number: (fill in area for text) / Contact Email (fill in area for text)
- Mailing address: (fill in area for text)
- Garaging location: (fill in area for text)
- Owner Name: (fill in area for text)
- Description of Operations: (fill in area for text)
- How long has the operation been in business? (fill in area for text)
- How many years of experience does your management have in the truck/transportation industry? (fill in area for text)
Coverages
Liability Combined Single Limit: ($1,000,000 (checkbox) / $500,000 (checkbox / $300,000 (checkbox) / Other: (fill in area for text)
Uninsured Motorist CSL: (fill in area for text) (checkbox for “Rejected”)
Medical Payments: (fill in area for text)
Physical Damage: (fill in area for text) (checkbox for Rejected)
Liability Deducible: ($500 checkbox, $1,000 checkbox, $2,500 checkbox, $5,000 checkbox)
Physical Damage Deductible: ($500 checkbox, $1,000 checkbox, $2,500 checkbox, $5,000 checkbox)
Driving radius: (fill in area for text)
How many years have you had your own continuous commercial auto insurance coverage for the current business name? (fill in area for text)
Do any of your vehicles travel across state lines? Yes (checkbox)/ No (checkbox)
If yes, please list all states in which vehicles operate: (fill in area for text)
What is the maximum radius traveled for your customer's business?
0-25 miles (checkbox)
26-50 miles (checkbox)
51-75 miles (checkbox)
76-100 miles (checkbox)
101-150 miles (checkbox)
151-200 miles (checkbox)
201-300 miles (checkbox)
300+ miles (checkbox)
Would you like physical damage coverage for this vehicle? (should be for each vehicle listed)
On the 2nd page of the application I would need the following:
I would need to have it where people can fill in the vehicle information such as VIN:, Year:, Make:, Model:, Type of Vehicle:, Trailers:, Value:
I would also need to have it where people can fill in the drivers with their driver info including Name:, DOB:, DL #:, DL State:, Class of License:, Married: Yes/No, Number of years driving similar vehicle:
Please make it where you can fill in 20 vehicle's information and 20 driver's info.
For the 2nd Application I would need one for Property Insurance
On the Commercial Property Application I would need the following:
- Building Address: (fill in area for text)
- Building Description: (fill in area for text)
- Building Amount: $(fill in area for text)
- Business Personal Property Amount: $ (fill in area for text) (checkbox for Not Needed)
- Building Sq Ft: (fill in area for text)
- Total Area Sq Ft: (fill in area for text)
- Building Construction Type: Wood Frame (checkbox), Steel (checkbox), Fire Resistive (checkbox), Non-Combustible (checkbox), Other (fill in area for text)
- # of stories: (fill in area for text)
- Year Built: (fill in area for text)
- Wiring improvement year: (fill in area for text)
- Roofing improvement year: (fill in area for text)
- Plumbing improvement year: (fill in area for text)
- Heating improvement year: (fill in area for text)
- What is to the right of the building and distance: (fill in area for text)
- What is to the left of the building and distance: (fill in area for text)
- What is in front of the building and distance: (fill in area for text)
- What is behind the building and distance: (fill in area for text)
- Burglar alarm installation and serviced by: (fill in area for text) None (checkbox)
- Does the premises have fire protection? Sprinkler system (checkbox), Fire detection (checkbox), Other: (fill in area for text) None (checkbox)

```html
<!DOCTYPE html>
<html lang="en">
<head>
<meta charset="utf-8">
<title>Commercial Auto and Property Insurance Application</title>
<link rel="stylesheet" href="https://fonts.googleapis.com/css2?family=Poppins:wght@400;500;600&display=swap">
<style>
:root{
  --navy:#1f3284;
  --green:#14963f;
  --row:#eef0f3;
  --ink:#2b2b2b;
  --rule:#555;
  --bg:#e9ece9;
  --paper:#ffffff;
}
*{box-sizing:border-box;margin:0;padding:0}
html,body{width:1200px;height:1200px;overflow:hidden}
body{background:var(--bg);font-family:"Poppins",sans-serif;color:var(--ink);position:relative}
.sheet{position:absolute;top:197px;width:570px;height:806px;background:var(--paper);padding:14px 16px;box-shadow:0 1px 3px rgba(0,0,0,.15);overflow:hidden}
.sheet--auto{left:20px}
.sheet--property{left:610px}

/* header */
.masthead{display:flex;justify-content:space-between;align-items:center;height:62px;border-bottom:2px solid #e2e5e2;margin-bottom:6px}
.brand{display:flex;align-items:center;gap:6px;font-weight:600;font-size:15px;color:var(--navy);padding-left:10px}
.brand__mark{width:9px;height:9px;background:var(--green)}
.contact{display:grid;grid-template-columns:22px auto;font-size:8px;line-height:12.5px;align-items:center}
.contact svg{width:12px;height:12px}

/* bands */
.band{color:#fff;text-align:center;font-size:13.5px;height:24px;line-height:24px;font-weight:500}
.band--navy{background:var(--navy)}
.band--green{background:var(--green)}
.band--blend{background:linear-gradient(90deg,var(--green),var(--navy))}
.band--note{font-size:9px;text-align:left;padding-left:10px}

/* rows */
.row{display:flex;align-items:flex-end;gap:6px;font-size:9.5px;height:23px;padding:0 2px 4px 10px;background:linear-gradient(var(--paper) 3px,var(--row) 3px)}
.row--plain{background:none}
.row--small{font-size:8.5px}
.row--tiny{font-size:7.5px;gap:4px}
.fill{flex:1;border-bottom:1px dashed var(--rule);height:1px;margin-bottom:3px}
.fill--fixed{flex:none}
.box{width:10px;height:10px;border:1px solid #444;flex:none;margin-bottom:1px;background:#fff}
.box--s{width:7px;height:7px}
.chip{background:#e6e8ec;padding:2px 8px}
.gap{flex:1}
.opt{display:flex;align-items:flex-end;gap:8px;font-size:8.5px}
.coverages{margin-top:7px}
.lines{display:grid;grid-template-columns:1fr 1fr 1fr;gap:8px 16px;padding:6px 10px 0}
.lines span{border-bottom:1px dashed var(--rule);height:18px}
.deduct{width:62px;text-align:center}

/* tables */
.tables{display:flex;gap:8px}
.grid{border-collapse:collapse;font-size:5.6px;font-weight:600;text-align:center;table-layout:fixed}
.grid th,.grid td{border:1px solid #444;padding:0}
.grid thead th{height:34px;font-size:5px;line-height:6px}
.grid tbody td{height:20.8px}
.grid .num{font-size:5.5px}
.grid--drivers{width:279px}
.grid--vehicles{width:255px}
.tables .band{font-size:11px;margin-bottom:5px}

/* property */
.sheet--property .band--blend{margin-top:5px}
.prop{font-size:8.6px;height:20px;display:flex;align-items:flex-end;gap:5px;padding-bottom:3px}
.prop .label{width:104px;flex:none}
.prop .chip{font-size:7.6px;padding:1px 5px}
.footer{display:flex;align-items:center;gap:8px;height:24px;margin-top:4px}
.footer__bar{flex:1;height:24px;background:linear-gradient(90deg,var(--green),var(--navy));color:#fff;font-size:8.4px;display:flex;align-items:center;gap:28px;padding-left:10px}
.footer__bar span{display:flex;align-items:center;gap:6px}
.footer__bar svg{width:10px;height:10px}
.footer .brand{font-size:10px;padding:0}
</style>
</head>
<body>

<section class="sheet sheet--auto">
  <header class="masthead">
    <div class="brand"><span class="brand__mark"></span>MEADOWLINE</div>
    <div class="contact">
      <svg viewBox="0 0 24 24"><path fill="#14963f" d="M12 2a7 7 0 0 0-7 7c0 5 7 13 7 13s7-8 7-13a7 7 0 0 0-7-7zm0 9.5A2.5 2.5 0 1 1 12 6.5a2.5 2.5 0 0 1 0 5z"/></svg>
      <span>Meadowline Insurance Services<br>2480 Orchard Ave Suite 110<br>Fairview, CA 90210</span>
      <svg viewBox="0 0 24 24"><path fill="#14963f" d="M6.6 10.8a15 15 0 0 0 6.6 6.6l2.2-2.2a1 1 0 0 1 1-.25 11.4 11.4 0 0 0 3.6.57 1 1 0 0 1 1 1V20a1 1 0 0 1-1 1A17 17 0 0 1 3 4a1 1 0 0 1 1-1h3.5a1 1 0 0 1 1 1c0 1.25.2 2.45.57 3.57a1 1 0 0 1-.25 1z"/></svg>
      <span>Tel: (555) 014-2290</span>
    </div>
  </header>

  <div class="band band--navy">COMMERCIAL AUTO INSURANCE APPLICATION</div>

  <div class="row">Business Name: <span class="fill"></span></div>
  <div class="row">Effective Date: <span class="fill"></span></div>
  <div class="row">How do you structure your business?
    <span class="opt" style="margin-left:8px">Sole Proprietor: <i class="box"></i></span>
    <span class="gap"></span><span class="opt">Partners: <i class="box"></i></span>
    <span class="gap"></span><span class="opt">Corporation: <i class="box"></i></span>
    <span class="gap"></span><span class="opt">LLC: <i class="box"></i></span></div>
  <div class="row">Contact Name: <span class="fill"></span></div>
  <div class="row">Phone Number: <span class="fill" style="flex:1.2"></span> Contact Email: <span class="fill"></span></div>
  <div class="row">Mailing address: <span class="fill"></span></div>
  <div class="row">Garaging location: <span class="fill"></span></div>
  <div class="row">Owner Name: <span class="fill"></span></div>
  <div class="row">Description of Operations: <span class="fill"></span></div>
  <div class="row">How long has the operation been in business? <span class="fill"></span></div>
  <div class="row">How many years of experience does your management have in the truck/transportation industry? <span class="fill"></span></div>

  <div class="band band--green coverages">COVERAGES:</div>

  <div class="row">Liability Combined Single Limit:
    <span class="chip">$1,000,000</span><i class="box"></i>
    <span class="chip">$500,000</span><i class="box"></i>
    <span class="chip">$300,000</span><i class="box"></i>
    <span class="chip">Other:</span><span class="fill"></span></div>
  <div class="row">Uninsured Motorist CSL: <span class="fill"></span> <span style="margin-left:14px">Rejected:</span> <i class="box"></i><span style="width:80px"></span></div>
  <div class="row">Medical Payments: <span class="fill"></span></div>
  <div class="row">Physical Damage: <span class="fill"></span> <span style="margin-left:14px">Rejected:</span> <i class="box"></i><span style="width:80px"></span></div>
  <div class="row">Liability Deducible: <span class="gap"></span>
    <span class="chip deduct">$500</span><i class="box"></i><span class="gap"></span>
    <span class="chip deduct">$1,000</span><i class="box"></i><span class="gap"></span>
    <span class="chip deduct">$2,500</span><i class="box"></i><span class="gap"></span>
    <span class="chip deduct">$5000</span><i class="box"></i></div>
  <div class="row">Physical Damage Deductible: <span class="gap"></span>
    <span class="chip deduct">$500</span><i class="box"></i><span class="gap"></span>
    <span class="chip deduct">$1,000</span><i class="box"></i><span class="gap"></span>
    <span class="chip deduct">$2,500</span><i class="box"></i><span class="gap"></span>
    <span class="chip deduct">$5000</span><i class="box"></i></div>
  <div class="row row--plain"><b style="font-weight:600">Driving radius:</b> <span class="fill" style="margin-right:10px"></span></div>
  <div class="row row--small">How many years have you had your own continuous commercial auto insurance coverage for the current business name?</div>
  <div class="row row--plain"><span class="fill"></span></div>
  <div class="row row--small">Do any of your vehicles travel across state lines? <span style="margin-left:30px">Yes</span> <i class="box"></i><span class="gap"></span>No <i class="box"></i><span style="width:70px"></span></div>
  <div class="row row--small">If yes, please list all states in which vehicles operate: <span class="fill"></span></div>
  <div class="row row--small">What is the maximum radius traveled for your customer's business?</div>
  <div class="row row--tiny row--plain">0-25 miles <i class="box box--s"></i> 26-50 miles <i class="box box--s"></i> 51-75 miles <i class="box box--s"></i> 76-100 miles <i class="box box--s"></i> 101-150 miles <i class="box box--s"></i> 151-200 miles <i class="box box--s"></i> 201-300 miles <i class="box box--s"></i> 300+ miles <i class="box box--s"></i></div>

  <div class="band band--blend band--note">Would you like physical damage coverage for this vehicle? (should be for each vehicle listed)</div>
  <div class="lines"><span></span><span></span><span></span><span></span><span></span><span></span></div>
</section>

<section class="sheet sheet--property">
  <div class="tables">
    <div>
      <div class="band band--navy">Driver information</div>
      <table class="grid grid--drivers">
        <colgroup><col style="width:17px"><col style="width:51px"><col style="width:34px"><col style="width:34px"><col style="width:34px"><col style="width:34px"><col style="width:17px"><col style="width:17px"><col style="width:35px"></colgroup>
        <thead><tr><th>S.No</th><th>Name:</th><th>DOB:</th><th>DL #:</th><th>DL State:</th><th>Class of License:</th><th colspan="2">Married:<br>Yes&nbsp;&nbsp;No</th><th>Number of years driving similar vehicle:</th></tr></thead>
        <tbody>
          <tr><td class="num">01</td><td></td><td></td><td></td><td></td><td></td><td></td><td></td><td></td></tr>
          <tr><td class="num">02</td><td></td><td></td><td></td><td></td><td></td><td></td><td></td><td></td></tr>
          <tr><td class="num">03</td><td></td><td></td><td></td><td></td><td></td><td></td><td></td><td></td></tr>
          <tr><td class="num">04</td><td></td><td></td><td></td><td></td><td></td><td></td><td></td><td></td></tr>
          <tr><td class="num">05</td><td></td><td></td><td></td><td></td><td></td><td></td><td></td><td></td></tr>
          <tr><td class="num">06</td><td></td><td></td><td></td><td></td><td></td><td></td><td></td><td></td></tr>
          <tr><td class="num">07</td><td></td><td></td><td></td><td></td><td></td><td></td><td></td><td></td></tr>
          <tr><td class="num">08</td><td></td><td></td><td></td><td></td><td></td><td></td><td></td><td></td></tr>
          <tr><td class="num">09</td><td></td><td></td><td></td><td></td><td></td><td></td><td></td><td></td></tr>
          <tr><td class="num">10</td><td></td><td></td><td></td><td></td><td></td><td></td><td></td><td></td></tr>
          <tr><td class="num">11</td><td></td><td></td><td></td><td></td><td></td><td></td><td></td><td></td></tr>
          <tr><td class="num">12</td><td></td><td></td><td></td><td></td><td></td><td></td><td></td><td></td></tr>
          <tr><td class="num">13</td><td></td><td></td><td></td><td></td><td></td><td></td><td></td><td></td></tr>
          <tr><td class="num">14</td><td></td><td></td><td></td><td></td><td></td><td></td><td></td><td></td></tr>
          <tr><td class="num">15</td><td></td><td></td><td></td><td></td><td></td><td></td><td></td><td></td></tr>
          <tr><td class="num">16</td><td></td><td></td><td></td><td></td><td></td><td></td><td></td><td></td></tr>
          <tr><td class="num">17</td><td></td><td></td><td></td><td></td><td></td><td></td><td></td><td></td></tr>
          <tr><td class="num">18</td><td></td><td></td><td></td><td></td><td></td><td></td><td></td><td></td></tr>
          <tr><td class="num">19</td><td></td><td></td><td></td><td></td><td></td><td></td><td></td><td></td></tr>
          <tr><td class="num">20</td><td></td><td></td><td></td><td></td><td></td><td></td><td></td><td></td></tr>
        </tbody>
      </table>
    </div>
    <div>
      <div class="band band--green">Vehicle information</div>
      <table class="grid grid--vehicles">
        <thead><tr><th>VIN:</th><th>Year:</th><th>Make:</th><th>Model:</th><th>Type of Vehicle:</th><th>Trailers:</th><th>Value:</th></tr></thead>
        <tbody>
          <tr><td></td><td></td><td></td><td></td><td></td><td></td><td></td></tr>
          <tr><td></td><td></td><td></td><td></td><td></td><td></td><td></td></tr>
          <tr><td></td><td></td><td></td><td></td><td></td><td></td><td></td></tr>
          <tr><td></td><td></td><td></td><td></td><td></td><td></td><td></td></tr>
          <tr><td></td><td></td><td></td><td></td><td></td><td></td><td></td></tr>
          <tr><td></td><td></td><td></td><td></td><td></td><td></td><td></td></tr>
          <tr><td></td><td></td><td></td><td></td><td></td><td></td><td></td></tr>
          <tr><td></td><td></td><td></td><td></td><td></td><td></td><td></td></tr>
          <tr><td></td><td></td><td></td><td></td><td></td><td></td><td></td></tr>
          <tr><td></td><td></td><td></td><td></td><td></td><td></td><td></td></tr>
          <tr><td></td><td></td><td></td><td></td><td></td><td></td><td></td></tr>
          <tr><td></td><td></td><td></td><td></td><td></td><td></td><td></td></tr>
          <tr><td></td><td></td><td></td><td></td><td></td><td></td><td></td></tr>
          <tr><td></td><td></td><td></td><td></td><td></td><td></td><td></td></tr>
          <tr><td></td><td></td><td></td><td></td><td></td><td></td><td></td></tr>
          <tr><td></td><td></td><td></td><td></td><td></td><td></td><td></td></tr>
          <tr><td></td><td></td><td></td><td></td><td></td><td></td><td></td></tr>
          <tr><td></td><td></td><td></td><td></td><td></td><td></td><td></td></tr>
          <tr><td></td><td></td><td></td><td></td><td></td><td></td><td></td></tr>
          <tr><td></td><td></td><td></td><td></td><td></td><td></td><td></td></tr>
        </tbody>
      </table>
    </div>
  </div>

  <div class="band band--blend">COMMERCIAL PROPERTY APPLICATION</div>

  <div class="prop"><span class="label">Business Name:</span><span class="fill"></span></div>
  <div class="prop"><span class="label">Building Address:</span><span class="fill"></span></div>
  <div class="prop"><span class="label">Building Description:</span><span class="fill"></span></div>
  <div class="prop"><span class="label">Building Amount: &nbsp;$</span><span class="fill fill--fixed" style="width:100px"></span>Business Personal Property Amount: $<span class="fill"></span> Not Needed <i class="box"></i></div>
  <div class="prop"><span class="label">Building Sq Ft:</span><span class="fill fill--fixed" style="width:160px"></span><span style="margin-left:16px">Total Area Sq Ft:</span><span class="fill"></span></div>
  <div class="prop">Building Construction Type: <span class="chip">Wood Frame</span><i class="box"></i><span class="chip">Steel</span><i class="box"></i><span class="chip">Fire Resistive</span><i class="box"></i><span class="chip">Non-Combustible</span><i class="box"></i><span class="chip">Other</span><i class="box"></i></div>
  <div class="prop"><span class="label">#Building of stories:</span><span class="fill"></span><span style="margin-left:8px">Year Built:</span><span class="fill"></span></div>
  <div class="prop">Plumbing improvement year: <span class="fill"></span><span style="margin-left:18px">Heating improvement year</span><span class="fill" style="flex:.6"></span></div>
  <div class="prop">What is to the right of the building and distance: <span class="fill" style="flex:.4"></span> What is to the left of the building and distance<span class="fill" style="flex:.4"></span></div>
  <div class="prop">What is in front of the building and distance: <span class="fill" style="flex:.4"></span> What is behind the building and distance:<span class="fill" style="flex:.6"></span></div>
  <div class="prop">Burglar alarm installation and serviced by: <span class="fill"></span><span style="margin-left:18px">None</span><i class="box"></i></div>
  <div class="prop">Does the premises have fire protection? <span class="chip">Sprinkler system</span><i class="box"></i><span class="chip">Fire detection</span><i class="box"></i><span class="chip">Other:</span><span class="fill"></span><span class="chip">None</span><i class="box"></i></div>

  <footer class="footer">
    <div class="footer__bar">
      <span><svg viewBox="0 0 24 24"><path fill="#fff" d="M6.6 10.8a15 15 0 0 0 6.6 6.6l2.2-2.2a1 1 0 0 1 1-.25 11.4 11.4 0 0 0 3.6.57 1 1 0 0 1 1 1V20a1 1 0 0 1-1 1A17 17 0 0 1 3 4a1 1 0 0 1 1-1h3.5a1 1 0 0 1 1 1c0 1.250.2 2.450.57 3.57a1 1 0 0 1-.25 1z"/></svg>Tel: (555) 014-2290</span>
      <span><svg viewBox="0 0 24 24"><path fill="#fff" d="M12 2a7 7 0 0 0-7 7c0 5 7 13 7 13s7-8 7-13a7 7 0 0 0-7-7zm0 9.5A2.5 2.5 0 1 1 12 6.5a2.5 2.5 0 0 1 0 5z"/></svg>2480 Orchard Ave Suite 110, Fairview, CA 90210</span>
    </div>
    <div class="brand"><span class="brand__mark"></span>MEADOWLINE</div>
  </footer>
</section>

</body>
</html>
```